Web Design Project - Shipping Industry

Goals and Objectives
The objective of the new website is to create a more modern look and feel. The site will also allow for a more effective means of communicating with members while providing the public with information and developments in the local, regional and international shipping industry.
Scope
The website will highlight the history of the organisation inclusive of text and photographs. It will take visitors through the years from beginning to present. Information on the history of the shipping industry will also be included.
It will feature current articles on the organisation, its members and stakeholders in the shipping industry. Member information as well as pertinent details regarding the organisation’s subsidiaries will be documented for the website.
Information as it relates to shipping statistics, case studies, laws and regulations, international treaties and trade documents, shipping terms, careers in shipping, job opportunities, training opportunities, information for shippers including port listing and trade lanes will be main features of the content for the website.
The Association’s community involvement, industry calendar events and related links relevant industry members will also be featured.
Target Market
• The General Public;
• Members of the organization;
• Shipping Industry Stakeholders (local, regional and international);
• Tertiary students conducting research.
• Potential employees
• Potential Business Partners
Best Practice Bench Marketing
The following websites are being looked at:
• Korvel Quayworks - http://www.korvelquayworks.example/ (preferred look)
• Tessaly Maritime Association - http://www.tma-freight.example/ (like image transition on main page)
• Drovna - http://www.drovna.example (professional look)
• PLW - http://www.pelworth.example (preferred color: blue in logo)
• Quillo - http://www.quillo.example/electronics/tv-video-audio/ (preferred look for links page: image + short text below + visit site link)
Expected Result
• 3 - 5 pages which must include: [1] main page [2] standard page [3] links page

```html
<!DOCTYPE html>
<html lang="en">
<head>
<meta charset="utf-8">
<title>Castrelle PCS</title>
<link rel="stylesheet" href="https://fonts.googleapis.com/css2?family=Open+Sans:wght@400&family=Arimo:wght@400&display=swap">
<style>
  :root {
    --bg-blue: #2a5690;
    --bg-blue-dark: #1f4678;
    --page: #ffffff;
    --logo: #2c4a7c;
    --nav-top: #4a74ad;
    --nav-bottom: #0f1f56;
    --nav-divider: #6f8fc0;
    --text: #555555;
    --heading: #333333;
    --heading-blue: #1f3a66;
    --link-red: #c1121c;
    --frame: #e6e6e6;
    --dot: #8a8a8a;
    --dot-active: #b3121b;
  }
  * { box-sizing: border-box; margin: 0; padding: 0; }
  html, body { width: 1019px; height: 1200px; overflow: hidden; }
  body {
    position: relative;
    background: linear-gradient(180deg, var(--bg-blue) 0%, var(--bg-blue-dark) 100%);
    font-family: "Arimo", Arial, sans-serif;
    color: var(--text);
  }
  .abs { position: absolute; }
  .page {
    left: 45px; top: 25px; width: 936px; height: 1122px;
    background: linear-gradient(180deg, #f1f1f1 0px, #ffffff 110px, #ffffff 100%);
    border: 1px solid #c9d3e0;
    box-shadow: 0 0 4px rgba(0,0,0,.4);
  }
  .logo {
    left: 90px; top: 55px;
    font-family: "Open Sans", Arial, sans-serif;
    font-size: 35px; color: var(--logo); letter-spacing: -0.5px;
  }
  .map-mark {
    left: 629px; top: 64px; width: 86px; height: 54px;
    background: radial-gradient(ellipse at center, #c8d3e0 0%, rgba(220,228,238,0) 70%);
  }
  .search {
    left: 730px; top: 78px; width: 236px; height: 22px; display: flex;
  }
  .search-field {
    width: 186px; height: 22px; background: #fff;
    border: 1px solid #cfcfcf; box-shadow: inset 0 1px 2px rgba(0,0,0,.15);
  }
  .search-button {
    width: 50px; height: 22px; background: #1c1c1c; color: #fff;
    font-size: 11px; line-height: 22px; text-align: center; font-family: "Arimo", Arial, sans-serif;
  }
  .nav {
    left: 59px; top: 139px; width: 910px; height: 41px;
    background: linear-gradient(180deg, var(--nav-top) 0%, #24427c 50%, var(--nav-bottom) 100%);
    display: flex; padding-left: 31px;
  }
  .nav-item {
    height: 41px; line-height: 41px; padding: 0 16px;
    color: #fff; font-size: 14px; border-right: 1px solid var(--nav-divider);
  }
  .nav-item.is-active {
    background: linear-gradient(180deg, #ffffff 0%, #dcdcdc 100%);
    color: #2c4a7c; border-right: none;
  }
  .slider-frame {
    left: 82px; top: 211px; width: 868px; height: 336px;
    background: #fff; border: 1px solid #eee;
    box-shadow: 0 6px 10px rgba(0,0,0,.12);
  }
  .slide-image {
    left: 98px; top: 228px; width: 840px; height: 305px;
    background: linear-gradient(180deg, #c9daee 0%, #b7cbe3 35%, #5f6d7b 60%, #2e3439 80%, #9aa3a8 100%);
    border: 1px solid #c4d0dc;
  }
  .slide-caption {
    left: 98px; top: 496px; width: 840px; height: 37px;
    background: rgba(60,60,60,.7); color: #fff; font-size: 13px;
    line-height: 37px; padding-left: 22px;
  }
  .slider-arrow { top: 348px; width: 42px; height: 42px; }
  .slider-arrow.prev { left: 39px; }
  .slider-arrow.next { left: 951px; }
  .slider-dots { left: 486px; top: 566px; display: flex; gap: 5px; }
  .dot { width: 11px; height: 11px; border-radius: 50%; background: var(--dot); box-shadow: inset 0 1px 1px rgba(0,0,0,.3); }
  .dot.is-active { background: var(--dot-active); }
  .feature { top: 594px; width: 250px; }
  .feature-title { font-size: 13px; color: var(--heading); height: 20px; }
  .feature-photo {
    margin-top: 7px; width: 243px; height: 137px; padding: 3px;
    background: #fff; border: 1px solid var(--frame); box-shadow: 0 1px 3px rgba(0,0,0,.12);
  }
  .feature-photo span { display: block; width: 100%; height: 100%; }
  .feature-text { margin-top: 12px; padding-left: 6px; font-size: 10.5px; line-height: 18px; width: 230px; }
  .feature-link { margin-top: 8px; padding-left: 6px; font-size: 10.5px; color: var(--link-red); }
  .about-title {
    left: 90px; top: 881px; font-size: 18px; color: var(--heading-blue);
    padding-bottom: 6px; border-bottom: 1px dotted #555; width: 230px;
  }
  .about-body { left: 87px; top: 924px; width: 850px; font-size: 11.5px; line-height: 24px; }
  .about-body p + p { margin-top: 23px; }
  .social { left: 54px; top: 1172px; display: flex; gap: 17px; }
  .social-icon { width: 22px; height: 22px; border-radius: 2px; background: #c9d6e8; }
  .copyright { right: 54px; top: 1171px; color: #fff; font-size: 10.5px; }
</style>
</head>
<body>
  <div class="abs page"></div>

  <header>
    <div class="abs logo">Castrelle PCS</div>
    <div class="abs map-mark" role="img" aria-label="Dotted world map decoration"></div>
    <div class="abs search">
      <div class="search-field"></div>
      <div class="search-button">SEARCH</div>
    </div>
    <nav class="abs nav">
      <div class="nav-item is-active">HOME</div>
      <div class="nav-item">ABOUT US</div>
      <div class="nav-item">SUSTAINABILITY</div>
      <div class="nav-item">NEWS</div>
      <div class="nav-item">CAREERS</div>
      <div class="nav-item">LINKS</div>
      <div class="nav-item" style="border-right:none">CONTACT US</div>
    </nav>
  </header>

  <section class="hero">
    <div class="abs slider-frame"></div>
    <div class="abs slide-image" role="img" aria-label="Container ship loaded with stacked containers at sea"></div>
    <div class="abs slide-caption">Nunc varius facilisis eros. Sed erat. In in velit quis arcu ornare laoreet. Curabitur adipiscing luctus massa.Integer ut purus ac augue commodo</div>
    <svg class="abs slider-arrow prev" viewBox="0 0 42 42">
      <path d="M42 0 A21 21 0 0 0 42 42 Z" fill="#3a3a3a"/>
      <path d="M36 16 L31 21 L36 26" stroke="#fff" stroke-width="3" fill="none"/>
    </svg>
    <svg class="abs slider-arrow next" viewBox="0 0 42 42">
      <path d="M0 0 A21 21 0 0 1 0 42 Z" fill="#3a3a3a"/>
      <path d="M6 16 L11 21 L6 26" stroke="#fff" stroke-width="3" fill="none"/>
    </svg>
    <div class="abs slider-dots">
      <span class="dot"></span><span class="dot"></span><span class="dot is-active"></span><span class="dot"></span><span class="dot"></span>
    </div>
  </section>

  <section class="features">
    <article class="abs feature" style="left:86px">
      <h3 class="feature-title" style="font-weight:400">LIFTING GLOBAL TRADE</h3>
      <div class="feature-photo"><span role="img" aria-label="Container ship sailing on grey water" style="background:linear-gradient(180deg,#c7ccd0 0%,#b9bec2 40%,#5a4f4a 60%,#25324a 75%,#8e958f 100%)"></span></div>
      <p class="feature-text">Nunc varius facilisis eros. Sed erat. In in velit quis arcu ornare laoreet. Curabitur adipiscing luctus massa.Integer ut purus ac commodo</p>
      <p class="feature-link">View More &gt;&gt;</p>
    </article>
    <article class="abs feature" style="left:379px">
      <h3 class="feature-title" style="font-weight:400">WE ARE CASTRELLE</h3>
      <div class="feature-photo"><span role="img" aria-label="Loaded container ship under blue sky" style="background:linear-gradient(180deg,#5c9ad2 0%,#7fb3e0 40%,#4a5560 62%,#2f5f6e 78%,#3f7f88 100%)"></span></div>
      <p class="feature-text">Nunc varius facilisis eros. Sed erat. In in velit quis arcu ornare laoreet. Curabitur adipiscing luctus massa.Integer ut purus ac commodo</p>
      <p class="feature-link">View More &gt;&gt;</p>
    </article>
    <article class="abs feature" style="left:684px">
      <h3 class="feature-title" style="font-weight:400">CASTRELLE SUPPLY SERVICE</h3>
      <div class="feature-photo"><span role="img" aria-label="Container ship with cranes in harbour" style="background:linear-gradient(180deg,#c4c8cc 0%,#b6babd 50%,#6a625c 68%,#2c3138 78%,#7d8286 100%)"></span></div>
      <p class="feature-text">Nunc varius facilisis eros. Sed erat. In in velit quis arcu ornare laoreet. Curabitur adipiscing luctus massa.Integer ut purus ac commodo</p>
      <p class="feature-link">View More &gt;&gt;</p>
    </article>
  </section>

  <section class="about">
    <h2 class="abs about-title" style="font-weight:400">ABOUT CASTRELLE PCS</h2>
    <div class="abs about-body">
      <p>Nunc varius facilisis eros. Sed erat. In in velit quis arcu ornare laoreet. Curabitur adipiscing luctus massa.Integer ut purus ac augue commodo commodo. Nunc nec mi eu justo tempor consectetuer. Etiam vitae nisl. In dignissim lacus ut ante. Cras elit lectus, bibendum a, adipiscing vitae, commodo et, dui.</p>
      <p>Lorem ipsum dolor sit amet, consectetuer adipiscing elit. Nam nibh. Nunc varius facilisis eros. Sed erat. In in velit quis arcu ornare laoreet. Curabitur adipiscing luctus massa.Lorem ipsum dolor sit amet, consectetuer adipiscing elit. Nam nibh. Nunc varius facilisis eros. Sed erat. In in velit quis arcu ornare laoreet. Curabitur adipiscing luctus massa. Lorem ipsum dolor sit amet, consectetuer adipiscing elit. Nam nibh. Nunc varius facilisis eros. Sed erat. In in velit quis arcu ornare laoreet. Curabitur adipiscing luctus massa.Lorem ipsum dolor sit amet, consectetuer adipiscing elit. Nam nibh. Nunc varius facilisis eros. Sed erat. In in velit quis arcu ornare laoreet. Curabitur adipiscing luctus massa.</p>
    </div>
  </section>

  <footer>
    <div class="abs social">
      <span class="social-icon" role="img" aria-label="Social network link"></span>
      <span class="social-icon" role="img" aria-label="Social network link"></span>
      <span class="social-icon" role="img" aria-label="Social network link"></span>
      <span class="social-icon" role="img" aria-label="Social network link"></span>
      <span class="social-icon" role="img" aria-label="Social network link"></span>
    </div>
    <div class="abs copyright">© 2012 Castrelle PCS, All Rights Reserved</div>
  </footer>
</body>
</html>
```